Need Business Card for our Real Estate Business with Sales Executive's Picture

PANTONE 484 C ( RED)

PANTONE 2766 C ( BLUE

Industry/Entity Type

Real Estate

Contact Information for Business Card

Name, Mobile, email, & picture of Person
Agency Phone, address, Web address

Requirements
Must have
• Our Logo Colours, Agent Picture,

```html
<!DOCTYPE html>
<html lang="en">
<head>
<meta charset="utf-8">
<title>Meridia Real Estate – Business Card</title>
<link href="https://fonts.googleapis.com/css2?family=Work+Sans:wght@400;500;600;700&display=swap" rel="stylesheet">
<style>
  :root{
    --navy:#101a4b;
    --red:#7e1b26;
    --white:#ffffff;
    --ink:#2a2f45;
    --stage:#e6e7ec;
    --photo-a:#3d5fa8;
    --photo-b:#dfe4ef;
  }
  *{box-sizing:border-box;margin:0;padding:0}
  html,body{width:1200px;height:900px;overflow:hidden}
  body{background:var(--stage);font-family:"Work Sans",sans-serif;position:relative}
  .card{position:absolute;width:620px;height:354px;border-radius:22px;overflow:hidden;box-shadow:0 10px 30px rgba(16,26,75,.18)}
  .card-front{left:290px;top:470px;background:var(--white)}
  .card-back{left:290px;top:76px;background:var(--navy);color:var(--white)}

  .agent-photo{position:absolute;left:0;top:0;width:270px;height:300px;
    background:linear-gradient(160deg,var(--photo-b) 0%,var(--photo-a) 70%)}
  .front-band{position:absolute;left:0;top:0;width:620px;height:354px}

  .wordmark{position:absolute;text-align:center;font-weight:600;letter-spacing:.14em}
  .wordmark .brand{display:block;font-size:46px;line-height:1}
  .wordmark .sub{display:block;font-size:11px;letter-spacing:.3em;margin-top:6px}
  .wordmark .mark-square{display:inline-block;width:9px;height:9px;background:var(--red);margin-right:10px;vertical-align:middle}
  .card-front .wordmark{right:52px;top:62px;color:var(--navy)}
  .card-back .wordmark{left:0;right:0;top:118px;color:var(--white)}
  .card-back .wordmark .mark-square{background:var(--white)}

  .agent{position:absolute;right:60px;top:168px;text-align:right;color:var(--navy)}
  .agent-name{font-size:25px;font-weight:700;letter-spacing:.02em;line-height:1.1}
  .agent-title{font-size:15px;font-weight:400;color:var(--ink);letter-spacing:.04em;margin-top:2px}
  .accent-tab{position:absolute;right:0;top:172px;width:30px;height:44px;background:var(--navy)}
  .accent-tab::before{content:"";position:absolute;left:-9px;top:0;width:3px;height:44px;background:var(--red)}

  .contacts{position:absolute;right:34px;top:232px;list-style:none;text-align:right;color:var(--ink)}
  .contacts li{font-size:14px;line-height:19px;display:flex;justify-content:flex-end;align-items:center;gap:10px;letter-spacing:.02em}
  .contacts svg{width:12px;height:12px;fill:var(--navy);flex:none}

  .address{position:absolute;left:0;right:0;bottom:40px;text-align:center;font-size:15px;letter-spacing:.04em}
</style>
</head>
<body>

<section class="card card-back" aria-label="Card back">
  <div class="wordmark">
    <span class="brand"><span class="mark-square"></span>MERIDIA</span>
    <span class="sub">REAL ESTATE</span>
  </div>
  <p class="address">Via dei Colli, 48. 12030 Borgo (CN)</p>
</section>

<section class="card card-front" aria-label="Card front">
  <div class="agent-photo" role="img" aria-label="Portrait photograph of the agent in a blue suit and striped tie"></div>
  <svg class="front-band" viewBox="0 0 620 354" aria-hidden="true">
    <path d="M0 196 L232 278 C258 288 266 306 296 306 L620 306 L620 354 L0 354 Z" fill="var(--navy)"/>
    <path d="M0 180 L246 268" stroke="var(--red)" stroke-width="5" fill="none"/>
  </svg>

  <div class="wordmark">
    <span class="brand"><span class="mark-square"></span>MERIDIA</span>
    <span class="sub">REAL ESTATE</span>
  </div>

  <div class="agent">
    <p class="agent-name">DANIEL REYES</p>
    <p class="agent-title">Managing Director</p>
  </div>
  <div class="accent-tab"></div>

  <ul class="contacts">
    <li>+852 2190 4417
      <svg viewBox="0 0 24 24"><path d="M6.6 10.8a15 15 0 0 0 6.6 6.6l2.2-2.2a1 1 0 0 1 1-.25 11.4 11.4 0 0 0 3.6.57 1 1 0 0 1 1 1V20a1 1 0 0 1-1 1A17 17 0 0 1 3 4a1 1 0 0 1 1-1h3.5a1 1 0 0 1 1 1c0 1.25.2 2.45.57 3.6a1 1 0 0 1-.25 1z"/></svg></li>
    <li>+852 2190 4418
      <svg viewBox="0 0 24 24"><path d="M6 2h12v6H6zM3 9h18v9h-3v4H6v-4H3zm5 6v5h8v-5z"/></svg></li>
    <li>info@meridiarealty.com
      <svg viewBox="0 0 24 24"><path d="M2 5h20v14H2zm2 2v.5l8 5 8-5V7zm0 2.8V17h16V9.8l-8 5z"/></svg></li>
    <li>www.meridiarealty.com
      <svg viewBox="0 0 24 24"><path d="M12 2a10 10 0 1 0 0 20 10 10 0 0 0 0-20zm7.9 9h-3.4a15 15 0 0 0-1.3-6 8 8 0 0 1 4.7 6zM12 4.1c1 1.3 2.2 3.9 2.5 6.9h-5C9.8 8 11 5.4 12 4.1zM8.8 5a15 15 0 0 0-1.3 6H4.1a8 8 0 0 1 4.7-6zM4.1 13h3.4a15 15 0 0 0 1.3 6 8 8 0 0 1-4.7-6zm7.9 6.9c-1-1.3-2.2-3.9-2.5-6.9h5c-.3 3-1.5 5.6-2.5 6.9zm3.2-.9a15 15 0 0 0 1.3-6h3.4a8 8 0 0 1-4.7 6z"/></svg></li>
  </ul>
</section>

</body>
</html>
```